pathology learning flashcard template graphic design .

Creative designs for 2 sides of the flashcards to include colorful sectioning and font sizes that will make it easy to use in studying.

```html
<!DOCTYPE html>
<html lang="en">
<head>
<meta charset="utf-8">
<title>Pathology Flashcard – Case 0001</title>
<link href="https://fonts.googleapis.com/css2?family=Source+Sans+3:ital,wght@0,400;0,700;1,400;1,700&family=Roboto+Condensed:wght@700&display=swap" rel="stylesheet">
<style>
  :root {
    --red: #e3101b;
    --pink: #f8dbe8;
    --ink: #111111;
    --frame: #555555;
    --paper: #ffffff;
  }
  * { margin: 0; padding: 0; box-sizing: border-box; }
  html, body { width: 863px; height: 1200px; overflow: hidden; background: var(--paper); }
  body { position: relative; font-family: "Source Sans 3", sans-serif; color: var(--ink); }

  .sheet { position: absolute; left: 0; width: 863px; border: 1px solid var(--frame); background: var(--paper); }
  .sheet--front { top: 0; height: 592px; }
  .sheet--back { top: 605px; height: 595px; }

  .card { position: absolute; left: 21px; width: 821px; border-radius: 34px; overflow: hidden; background: var(--paper); }
  .card--front { top: 20px; height: 551px; border: 3.5px solid var(--ink); }
  .card--back { top: 20px; height: 551px; border: 3.5px solid var(--red); }

  .ln { display: block; white-space: nowrap; text-align: justify; text-align-last: justify; }
  .ln.end { text-align-last: left; }

  /* front */
  .question-panel { position: absolute; left: 343px; top: 0; right: 0; bottom: 0; background: var(--pink); }
  .category { position: absolute; left: 19px; top: 20px; font-family: "Roboto Condensed", sans-serif; font-weight: 700; font-size: 35px; color: var(--red); }
  .organ-art { position: absolute; left: 75px; top: 67px; width: 196px; height: 196px; border-radius: 50%; border: 3px solid var(--red); background: radial-gradient(circle at 50% 50%, #ffffff 0%, #eeeeee 45%, var(--pink) 75%); }
  .case-band { position: absolute; left: 0; top: 281px; width: 343px; height: 46px; background: var(--pink); }
  .case-band span { position: absolute; left: 16px; top: 6px; font-weight: 700; font-style: italic; font-size: 25.5px; }
  .patient-avatar { position: absolute; left: 88px; top: 336px; width: 168px; height: 168px; border-radius: 50%; background: radial-gradient(circle at 50% 60%, #dcdcdc 0%, #c4c4c4 35%, var(--pink) 62%); }
  .sex-icon { position: absolute; left: 31px; top: 400px; }
  .age { position: absolute; left: 0; width: 346px; top: 504px; text-align: center; font-family: "Roboto Condensed", sans-serif; font-weight: 700; font-size: 23px; }

  .question { position: absolute; left: 17px; top: 14px; width: 440px; font-size: 21px; line-height: 26.2px; }
  .options { position: absolute; left: 17px; top: 414px; font-size: 22px; line-height: 27.6px; list-style: none; }

  /* back */
  .diagnosis { position: absolute; left: 17px; top: 14px; font-weight: 700; font-style: italic; font-size: 38px; color: var(--red); }
  .column { position: absolute; top: 66px; width: 379px; font-size: 16px; line-height: 19.1px; }
  .column--left { left: 14px; }
  .column--right { left: 421px; }
  .column h3 { font-size: 16px; font-weight: 700; font-style: italic; line-height: 19.1px; }
  .column p + h3 { margin-top: 19.1px; }
  .gap-top { margin-top: 19.1px; }

  .answer-band { position: absolute; left: 0; right: 0; top: 355px; bottom: 0; background: var(--pink); }
  .answer { position: absolute; left: 14px; top: 10px; width: 786px; font-size: 16px; line-height: 19.1px; }
  .answer h3 { font-size: 16px; font-weight: 700; font-style: italic; }
  .answer p { font-style: italic; }
  .sources { position: absolute; left: 14px; top: 150px; font-size: 12.5px; }
  .card-number { position: absolute; left: 769px; top: 498px; }
</style>
</head>
<body>

<section class="sheet sheet--front">
  <div class="card card--front">
    <div class="question-panel">
      <p class="question">
        <span class="ln">50-year-old woman comes to the clinic</span>
        <span class="ln">because she has difficulty swallowing for</span>
        <span class="ln">the past few months. She says symptoms</span>
        <span class="ln">have been worsening. She also complains of</span>
        <span class="ln">cough, <em>mostly at night and in fear of choking,</em></span>
        <span class="ln"><em>has stopped eating many foods,</em> losing about</span>
        <span class="ln">12 lbs in the past 3 months. Past medical</span>
        <span class="ln">history is unremarkable. Vital signs are</span>
        <span class="ln">normal and physical exam is unremarkable.</span>
        <span class="ln">Chest x-ray with demonstrates an <em>air-fluid</em></span>
        <span class="ln"><em>level, while manometry shows absent relaxa-</em></span>
        <span class="ln"><em>tion of the</em> lower esophageal sphincter</span>
        <span class="ln">during swallowing. What is the most likely</span>
        <span class="ln end">diagnosis?</span>
      </p>
      <ul class="options">
        <li>A) GERD</li>
        <li>B) Barret Esophagus</li>
        <li>C) Achalasia</li>
        <li><em>D) Eosinophilic esophagitis</em></li>
      </ul>
    </div>
    <h1 class="category">GASTROINTESTINAL</h1>
    <div class="organ-art" role="img" aria-label="Illustration of a stomach with bacteria and microbes inside"></div>
    <div class="case-band"><span>PATHOLOGY CASE ID 0001</span></div>
    <svg class="sex-icon" width="40" height="64" viewBox="0 0 40 64" aria-label="Female">
      <circle cx="20" cy="19" r="16" fill="none" stroke="#111" stroke-width="4"/>
      <line x1="20" y1="35" x2="20" y2="62" stroke="#111" stroke-width="4"/>
      <line x1="8" y1="50" x2="32" y2="50" stroke="#111" stroke-width="4"/>
    </svg>
    <div class="patient-avatar" role="img" aria-label="Illustrated portrait of the female patient"></div>
    <p class="age">Age: 50 years</p>
  </div>
</section>

<section class="sheet sheet--back">
  <div class="card card--back">
    <h2 class="diagnosis">Achalasia</h2>

    <div class="column column--left">
      <h3>Definition:</h3>
      <p>
        <span class="ln"><em>Motility disorder where esophageal relaxation is</em></span>
        <span class="ln end"><em>impaired in the lower esophageal</em> sphincter (LES).</span>
      </p>
      <h3>Etiology/Pathology:</h3>
      <p>
        <span class="ln"><em>Destruction of inhibitory neurons in the Auerbach</em></span>
        <span class="ln"><em>plexus.</em> Loss of peristalsis in the lower esophageal</span>
        <span class="ln end">sphincter (lower two thirds of the esophagus).</span>
      </p>
      <h3>P/E and Symptoms:</h3>
      <p>
        <span class="ln">Dysphagia that is progressive, regurgitation,</span>
        <span class="ln">weight-loss, dry cough, chest pain, GERD,</span>
        <span class="ln">esophageal perforation, squamous cell carcinoma,</span>
        <span class="ln end">aspiration pneumonia.</span>
      </p>
    </div>

    <div class="column column--right">
      <p class="gap-top">
        <span class="ln"><em>Barium swallow will show ‘bird’s beak’ and</em></span>
        <span class="ln"><em>esophageal dilation. Manometry will present with</em></span>
        <span class="ln"><em>increased resting lower esophageal</em> sphincter</span>
        <span class="ln">pressure. Endoscopy will usually present with</span>
        <span class="ln">normal <em>mucosa and LES dilation, and in some cases</em></span>
        <span class="ln"><em>residual material such as undigested food particles</em></span>
        <span class="ln end"><em>may be present.</em></span>
      </p>
      <h3>Rx:</h3>
      <p>
        <span class="ln"><em>First line of treatment are nitrates, calcium channel</em></span>
        <span class="ln"><em>blockers, and Botulinum toxin injection in the LES.</em></span>
        <span class="ln"><em>Long term management options include esophageal</em></span>
        <span class="ln end"><em>dilation with pneumatic balloon and myotomy.</em></span>
      </p>
    </div>

    <div class="answer-band">
      <div class="answer">
        <h3>C-Achalasia</h3>
        <p>
          <span class="ln">Symptoms and studies suggestive of achalasia. Patient’s manometry presents with no relaxation of the lower</span>
          <span class="ln">esophageal sphincter during swallowing. Patient also complains of dysphagia and is unable to swallow</span>
          <span class="ln">properly, leading to weight loss. Patient has no past infection or inflammation, ruling out eosinophilic</span>
          <span class="ln">esophagitis. Patient does not have GERD, eliminating the possibility of Barrett esophagus, in which at least 5</span>
          <span class="ln end">years of acid reflux are beforehand to develop columnar metaplasia.</span>
        </p>
      </div>
      <p class="sources">Sources: Harlow’s Drug Guide;Pellman Pocket Formulary;Medlexa.example;Clinivue.example</p>
    </div>
  </div>

  <svg class="card-number" width="72" height="72" viewBox="0 0 72 72" aria-label="Card 1">
    <circle cx="36" cy="36" r="33" fill="#ffffff" stroke="#e3101b" stroke-width="3.5"/>
    <text x="36" y="52" text-anchor="middle" font-family="Source Sans 3, sans-serif" font-weight="700" font-size="44" fill="#111">1</text>
  </svg>
</section>

</body>
</html>
```